Business Card Design - Amberfield Court

We are looking at a new design for our business cards that has a modern and professional look. We run a residential aged care facility focussing on the care of residents. The cards will be used for potential clients, consultants and business opportunities in this sector. Blue and white is our main colours and would to see these colours incorporated in the design.
Industry/Entity Type
Business
Contact Information for Business Card
Amberfield Court, Darren Walsh, dwalsh@amberfieldcourt.com.au, Finance Manager, 0472 639 208, BCom, 37 Marrabel Crescent, Brindle Vale, Qld 4093.
Look and feel
Each slider illustrates characteristics of the customer's brand and the style your logo design should communicate.

```html
<!DOCTYPE html>
<html lang="en">
<head>
<meta charset="utf-8">
<title>Amberfield Court – Business Card</title>
<link href="https://fonts.googleapis.com/css2?family=Source+Sans+3:wght@300;400;600&display=swap" rel="stylesheet">
<style>
  :root {
    --backdrop: #1c1c1c;
    --card-white: #ffffff;
    --brand-blue: #4e7b96;
    --name-blue: #3e6f8c;
    --ink: #1b1b1b;
    --wordmark-navy: #1d3347;
  }
  * { margin: 0; padding: 0; box-sizing: border-box; }
  html, body { width: 1200px; height: 900px; overflow: hidden; }
  body {
    background: var(--backdrop);
    font-family: "Source Sans 3", "Myriad Pro", sans-serif;
    position: relative;
  }
  .card {
    position: absolute;
    top: 170px;
    width: 347px;
    height: 561px;
  }
  .card--front { left: 259px; background: var(--card-white); }
  .card--back { left: 631px; background: var(--brand-blue); }

  .tab {
    position: absolute;
    left: 102px;
    width: 143px;
    height: 29px;
    background: var(--brand-blue);
  }
  .tab--top { top: 0; }
  .tab--bottom { bottom: 0; }

  .wordmark {
    position: absolute;
    font-weight: 300;
    text-transform: uppercase;
    letter-spacing: 2px;
    line-height: 1;
    white-space: nowrap;
  }
  .card--front .wordmark {
    left: 0; right: 0;
    top: 188px;
    text-align: center;
    font-size: 29px;
    color: var(--wordmark-navy);
  }
  .card--back .wordmark {
    left: 27px;
    top: 458px;
    font-size: 30px;
    color: var(--card-white);
  }

  .contact {
    position: absolute;
    left: 0; right: 0;
    top: 318px;
    text-align: center;
    color: var(--ink);
    font-size: 15.5px;
    line-height: 23px;
  }
  .contact__name {
    color: var(--name-blue);
    font-weight: 600;
    font-size: 21px;
    line-height: 26px;
  }
  .contact__credential { font-size: 15px; }
  .contact__role { margin-bottom: 21px; }
  .contact__address { margin-bottom: 19px; }
  .contact__line { display: flex; align-items: center; justify-content: center; gap: 4px; }
  .icon { width: 12px; height: 12px; fill: var(--brand-blue); }
</style>
</head>
<body>
  <section class="card card--front" aria-label="Card front">
    <div class="tab tab--top"></div>

    <div class="wordmark">Amberfield Court</div>

    <div class="contact">
      <div class="contact__name">Darren Walsh, <span class="contact__credential">BCom</span></div>
      <div class="contact__role">Finance Manager</div>
      <div class="contact__address">37 Marrabel Crescent,<br>Brindle Vale, Qld 4093</div>
      <div class="contact__line">
        <svg class="icon" viewBox="0 0 24 24" aria-hidden="true"><path d="M6.6 10.8a15.1 15.1 0 0 0 6.6 6.6l2.2-2.2c.3-.3.7-.4 1-.2 1.1.4 2.3.6 3.6.6.6 0 1 .4 1 1V20c0 .6-.4 1-1 1C10.6 21 3 13.4 3 4c0-.6.4-1 1-1h3.5c.6 0 1 .4 1 1 0 1.3.2 2.5.6 3.6.1.3 0 .7-.2 1z"/></svg>
        <span>0472 639 208</span>
      </div>
      <div class="contact__line">
        <svg class="icon" viewBox="0 0 24 24" aria-hidden="true"><path d="M2 5h20v14H2z"/><path d="M3 6l9 7 9-7" fill="none" stroke="#fff" stroke-width="1.6"/></svg>
        <span>dwalsh@amberfieldcourt.com.au</span>
      </div>
    </div>

    <div class="tab tab--bottom"></div>
  </section>

  <section class="card card--back" aria-label="Card back">
    <div class="wordmark">Amberfield Court</div>
  </section>
</body>
</html>
```